BW PowerPoint Template Refresh

I'm looking to refresh our corporate presentation collateral, namely our base PowerPoint template. I need something that sparks, and gives the appearance of our contemporary firm that is hip, innovative, and modern. The project should provide for the various slide master templates with appropriately sized background images for slides in 4:3 and 16:9 formats

Target Market(s)

Investment banking prospect and clients which are typically in the high-tech industries of software, semiconductors,telecom, and telecom components

Industry/Entity Type

Investment Banking

Font styles to use
Other font styles liked:
• Goudy Old Style

Requirements
Must have
• - Must leverage current logo (red color is the standard, however portions of the logo or, color variations from our stock are possible for use), primary and secondary current colors. Non-section text is Goudy Old Style (headers and body text)
- The PPT template must have at least all of the LAYOUT options found in the Old BW Prez
- Options with and without the Brenwick logo as a transparent background
- Need a final version in 16:9 and 4:3 formats
- Must be able to add footer information such as "Confidential Information", slide number, and date
Nice to have
• a few design ideas on the IP Engineering image found on slide 7 of the New BW Prez Attempt.ppt file

```html
<!DOCTYPE html>
<html lang="en">
<head>
<meta charset="utf-8">
<title>KX Relay Lantern Buy-Side Process</title>
<link rel="stylesheet" href="https://fonts.googleapis.com/css2?family=Sorts+Mill+Goudy&display=swap">
<style>
  :root {
    --band-red: #ff2d1a;
    --band-mid: #d9405e;
    --band-blue: #2f5a9e;
    --brand-red: #b5232b;
    --brand-navy: #1f3f73;
    --ink: #1a1a1a;
    --rule: #2d4a7a;
    --paper: #ffffff;
    --art-light: #f2f2f2;
    --art-dark: #bdbdbd;
  }
  * { margin: 0; padding: 0; box-sizing: border-box; }
  html, body { width: 1200px; height: 675px; overflow: hidden; background: var(--paper); }
  body { font-family: "Sorts Mill Goudy", "Goudy Old Style", Georgia, serif; color: var(--ink); }
  .slide { position: relative; width: 1200px; height: 675px; overflow: hidden; background: var(--paper); }

  .title-band {
    position: absolute; left: 0; top: 0; width: 1200px; height: 98px;
    background: linear-gradient(90deg, var(--band-red) 0%, var(--band-mid) 40%, var(--band-blue) 100%);
  }
  .title-band h1 {
    position: absolute; left: 50px; top: 36px;
    font-weight: 400; font-size: 21px; color: #fff; letter-spacing: 0.2px;
  }

  .feature-art {
    position: absolute; left: 763px; top: 98px; width: 437px; height: 577px;
    background: radial-gradient(circle at 65% 55%, var(--art-dark) 0%, #d6d6d6 35%, var(--art-light) 75%);
  }

  .brand { position: absolute; text-align: center; line-height: 1; }
  .brand .name { color: var(--brand-red); font-size: 24px; letter-spacing: 0.5px; }
  .brand .sub { color: var(--brand-navy); font-size: 19px; margin-top: 3px; }
  .brand-main { left: 280px; top: 124px; width: 200px; }
  .brand-main .sub { font-size: 15px; letter-spacing: 1px; }
  .brand-left { left: 140px; top: 270px; width: 200px; }
  .brand-right { left: 417px; top: 270px; width: 200px; }
  .brand-right .sub { font-size: 16px; }

  .org-lines { position: absolute; left: 0; top: 0; }

  .service-list {
    position: absolute; list-style: none; font-size: 16px; line-height: 21px;
  }
  .service-list li { position: relative; padding-left: 19px; }
  .service-list li::before {
    content: ""; position: absolute; left: 0; top: 7px;
    width: 6px; height: 6px; background: var(--ink);
  }
  .list-core { left: 57px; top: 337px; width: 300px; }
  .list-plus { left: 430px; top: 337px; width: 310px; }
</style>
</head>
<body>
<div class="slide">
  <header class="title-band">
    <h1>KX Relay™ Lantern Buy-Side Process: A Complete Summary</h1>
  </header>

  <div class="feature-art" role="img" aria-label="Grey engineering illustration of interlocking gears and hexagon patterns"></div>

  <div class="brand brand-main">
    <div class="name">KX Relay™</div>
    <div class="sub">TRANSACTIONS</div>
  </div>

  <svg class="org-lines" width="1200" height="675" aria-hidden="true">
    <g stroke="var(--rule)" stroke-width="2" fill="none">
      <line x1="380" y1="172" x2="380" y2="221"/>
      <line x1="243" y1="221" x2="517" y2="221"/>
      <line x1="243" y1="220" x2="243" y2="257"/>
      <line x1="517" y1="220" x2="517" y2="257"/>
    </g>
    <line x1="382" y1="273" x2="382" y2="642" stroke="var(--rule)" stroke-width="1"/>
  </svg>

  <div class="brand brand-left">
    <div class="name">KX Relay™</div>
    <div class="sub">Lantern</div>
  </div>
  <div class="brand brand-right">
    <div class="name">KX Relay™</div>
    <div class="sub">Lantern Plus</div>
  </div>

  <ul class="service-list list-core">
    <li>Acquisition Criteria Development</li>
    <li>Industry Analysis and Market Research</li>
    <li>Target Company List Development</li>
    <li>Target Company Research</li>
    <li>Target Company Approach</li>
    <li>Acquisition Lead Presentation and Reports</li>
  </ul>

  <ul class="service-list list-plus">
    <li>Acquisition Criteria Development</li>
    <li>Industry Analysis and Market Research</li>
    <li>Target Company List Development</li>
    <li>Target Company Research</li>
    <li>Target Company Approach</li>
    <li>Acquisition Lead Presentation and Reports</li>
    <li>Due Diligence Services</li>
    <li>Financial Analysis and Modeling</li>
    <li>Acquisition Valuation</li>
    <li>Acquisition Financing (Capital Raising)</li>
    <li>Acquisition Closing Consultation</li>
    <li>Corporate Governance (Board of Directors &amp; Management Recruiting)</li>
  </ul>
</div>
</body>
</html>
```